Wholesale Catalogue Design for Greeting Cards

Fern Ink is a small letterpress printery, I would like to have a wholesale catalogue designed for my range of letterpress greeting cards. I currently have 30 cards in my collection, I can supply photos, I want to be able to add to the catalogue in the future. I also want the design to represent my card designs: fun, colourful and with an elegant edge, featuring a mix of my original illustrations and hand lettering along with downloadable designs and fonts.
I would like to be able to email the catalogue to my wholesale customers and to be able to print the catalogue to use with new/potential wholesale customers.

Target Market(s)

Small boutique retailers, gift shops, baby/kids gift shops, florists

Industry/Entity Type

Wholesale

Font styles to use
Serif

Colors
eea4c8

Requirements
Must have
• I have been using baskerville font in my branding, so it would be good to include this in the design. I can provide photos and text. I also have a pink and black logo (seen attached), it would be great if the design can incorporate some of the same colour scheme.
Nice to have
• I have added some pics below of other catalogues I like the layout of.
• You can also view my work at craftly.com/fernink or ferninkdesign.com
• * I believe I have now loaded all the relevant photos and info
• ** I have uploaded some pics of my attempt at a wholesale catalogue and my current order sheet as this outlines the products I want in the catalogue and the different card sections. my catalogue attempt has more recent photos. I will upload photos of the remaining products by end of today (27.2.16)

```html
<!DOCTYPE html>
<html lang="en">
<head>
<meta charset="utf-8">
<title>Fern Ink – 2016 Wholesale Catalogue</title>
<link rel="stylesheet" href="https://fonts.googleapis.com/css2?family=Libre+Baskerville:wght@400;700&display=swap">
<style>
  :root {
    --paper: #ffffff;
    --brand-pink: #e6a3a3;
    --ribbon-pink: #e8b3b2;
    --logo-panel: #fbf3f2;
    --ink: #111111;
    --timber-dark: #858382;
    --timber-light: #aeacab;
    --envelope-pink: #d7a1c3;
    --card-white: #efedec;
    --card-highlight: #f8f7f6;
  }
  html, body {
    margin: 0;
    padding: 0;
    overflow: hidden;
    background: var(--paper);
  }
  .catalogue-cover {
    position: relative;
    width: 1200px;
    height: 918px;
    overflow: hidden;
    background: var(--paper);
    font-family: "Libre Baskerville", "Baskerville", Georgia, serif;
    color: var(--ink);
  }
  .cover-shapes {
    position: absolute;
    inset: 0;
    width: 1200px;
    height: 918px;
  }
  .brand-panel {
    position: absolute;
    left: 122px;
    top: 73px;
    width: 411px;
    height: 84px;
    background: var(--logo-panel);
    display: flex;
    align-items: center;
    justify-content: center;
  }
  .brand-name {
    margin: 0;
    font-weight: 400;
    font-size: 50px;
    line-height: 1;
    color: var(--brand-pink);
  }
  .catalogue-title {
    position: absolute;
    left: 262px;
    top: 200px;
    width: 558px;
    height: 57px;
    margin: 0;
    display: flex;
    align-items: center;
    justify-content: center;
    font-weight: 700;
    font-size: 31px;
    color: var(--paper);
    letter-spacing: 0.3px;
  }
  .tagline {
    position: absolute;
    left: 147px;
    top: 694px;
    margin: 0;
    font-weight: 700;
    font-size: 23px;
    line-height: 35px;
  }
  .website {
    position: absolute;
    left: 147px;
    top: 810px;
    margin: 0;
    font-weight: 400;
    font-size: 21px;
  }
</style>
</head>
<body>
  <main class="catalogue-cover">
    <svg class="cover-shapes" viewBox="0 0 1200 918">
      <defs>
        <linearGradient id="cardPhotoTone" x1="0" y1="0" x2="1" y2="1">
          <stop offset="0" stop-color="var(--timber-dark)"/>
          <stop offset="0.32" stop-color="var(--timber-light)"/>
          <stop offset="0.46" stop-color="var(--envelope-pink)"/>
          <stop offset="0.56" stop-color="var(--card-white)"/>
          <stop offset="1" stop-color="var(--card-highlight)"/>
        </linearGradient>
      </defs>
      <polygon class="photo-frame" points="418,0 1200,0 1200,918 662,918 238,480" fill="var(--ribbon-pink)"/>
      <polygon class="feature-photo" points="452,0 1200,0 1200,918 692,918 266,480"
               fill="url(#cardPhotoTone)" role="img"
               aria-label="Photo of a white letterpress card printed with pink hand-lettered 'I love you' and a small red heart, on a pink envelope over grey timber"/>
      <polygon class="title-ribbon" points="227,200 820,200 820,257 227,257 262,228.5" fill="var(--ribbon-pink)"/>
    </svg>

    <div class="brand-panel">
      <p class="brand-name">Fern Ink</p>
    </div>

    <h1 class="catalogue-title">2016 Wholesale Catalogue</h1>

    <p class="tagline">There is no excuse for<br>giving boring cards</p>

    <p class="website">www.fernink.com/au</p>
  </main>
</body>
</html>
```